Falbrook Company Notepad / Grid pad / Graph pad

I need a "modern" version of this graph pad. The information at the top needs to be shown, along with the graph lines, however, I need this more "interesting" than it currently is. This will be printed and bound at the TOP edge with 50 sheets per pack.

Target Market(s)

Clients - Want to show sophistication and not childish.

Industry/Entity Type

Structural Engineering

Font styles to use
Sans Serif

Colors
0255a3
85abd2

Requirements
Must have
• My project must have all of the elements currently shown on the pdf
Should not have
• My project should not have clipart images.

Files

```html
<!DOCTYPE html>
<html lang="en">
<head>
<meta charset="utf-8">
<title>Falbrook Company Graph Pad</title>
<link href="https://fonts.googleapis.com/css2?family=Source+Sans+3:wght@400;600;700&display=swap" rel="stylesheet">
<style>
  :root{
    --backdrop:#aaa9a9;
    --paper:#f5f4f2;
    --navy:#1f5274;
    --label-blue:#1f4f7a;
    --ink:#1a1a1a;
    --rule:#3a3a3a;
    --grid-line:#c9c9c9;
    --grid-frame:#7d7d7d;
    --tagline:#7a8088;
  }
  *{margin:0;padding:0;box-sizing:border-box}
  html,body{width:956px;height:1200px;overflow:hidden;background:var(--backdrop)}
  body{font-family:"Source Sans 3",sans-serif;position:relative}
  .sheet{
    position:absolute;left:94px;top:51px;width:775px;height:1092px;
    background:var(--paper);box-shadow:0 4px 14px rgba(0,0,0,.35);overflow:hidden;
  }
  .brand{position:absolute;left:62px;top:66px}
  .brand-name{font-size:25px;font-weight:700;color:var(--navy);line-height:1.05;letter-spacing:.5px}
  .brand-tagline{margin-top:8px;font-size:8px;font-weight:600;color:var(--tagline);letter-spacing:.2px}
  .contact{position:absolute;left:331px;top:39px;font-size:12.5px;color:var(--ink);line-height:16.8px}
  .contact .web-block{margin-top:11px}
  .divider{position:absolute;left:498px;top:39px;width:1px;height:116px;background:#8c8c8c}
  .job-fields{position:absolute;left:522px;top:33px;width:300px}
  .field{display:flex;align-items:flex-end;height:21.5px;font-size:12.5px;color:var(--label-blue)}
  .field .label{width:46px}
  .field .line{border-bottom:1px solid var(--rule);height:1px;margin-bottom:4px;width:146px}
  .field .line.short{width:57px}
  .field .of{margin:0 10px}
  .field .line.tail{width:56px}
  .grid{
    position:absolute;left:56px;top:195px;width:669px;height:793px;
    border:1.3px solid var(--grid-frame);
    background-color:var(--paper);
    background-image:
      linear-gradient(to right,var(--grid-line) 1px,transparent 1px),
      linear-gradient(to bottom,var(--grid-line) 1px,transparent 1px);
    background-size:20.87px 17.23px;
    background-position:-1px -1px;
  }
  .footer-band{position:absolute;left:0;bottom:0;width:775px;height:62px;display:block}
</style>
</head>
<body>
  <div class="sheet">
    <div class="brand">
      <div class="brand-name">FALBROOK<br>COMPANY</div>
      <div class="brand-tagline">Structures | Precise | Trusted</div>
    </div>

    <div class="contact">
      <div>215 Alder Avenue</div>
      <div>Suite 304</div>
      <div>Harbor Point</div>
      <div>FL 33990</div>
      <div class="web-block">555.014.2290</div>
      <div>www.falbrookcompany.com</div>
    </div>

    <div class="divider"></div>

    <div class="job-fields">
      <div class="field"><span class="label">Project</span><span class="line"></span></div>
      <div class="field"><span class="label">Task</span><span class="line"></span></div>
      <div class="field"><span class="label">Page</span><span class="line short"></span><span class="of">of</span><span class="line tail"></span></div>
      <div class="field"><span class="label">Job No</span><span class="line"></span></div>
      <div class="field"><span class="label">Author</span><span class="line"></span></div>
      <div class="field"><span class="label">Date</span><span class="line"></span></div>
    </div>

    <div class="grid"></div>

    <svg class="footer-band" viewBox="0 0 775 62" preserveAspectRatio="none" aria-hidden="true">
      <path fill="var(--navy)" d="M0 40 C260 26 520 20 775 14 L775 62 L0 62 Z"/>
    </svg>
  </div>
</body>
</html>
```